Letterhead for Conveyancing Company

Use existing logo to create a letterhead for a conveyancing company. Must be able to be used in Microsoft Word. Easy to read and professional.
Contact information to be at the bottom.
Bright Oak Conveyancing Pty Ltd
ACN 621 984 736PO Box 535 Campbelltown SA 5074
Mobile - 0461739286
Web address - www.brightoakconveyancing.com.au

Requirements
Must have
• Logo and contact details.
• Simple and professional.

```html
<!DOCTYPE html>
<html lang="en">
<head>
<meta charset="utf-8">
<title>Bright Oak Conveyancing Letterhead</title>
<link href="https://fonts.googleapis.com/css2?family=Open+Sans:wght@400;600&family=Lato:wght@400&display=swap" rel="stylesheet">
<style>
  :root {
    --brand-pink: #e2409a;
    --brand-grey: #878787;
    --ink: #4a4a4a;
    --ink-strong: #2f2f2f;
    --paper: #ffffff;
  }
  * { margin: 0; padding: 0; box-sizing: border-box; }
  html, body { width: 1040px; height: 1200px; overflow: hidden; background: var(--paper); }
  .letterhead {
    position: relative;
    width: 1040px;
    height: 1200px;
    background: var(--paper);
    font-family: "Open Sans", Arial, sans-serif;
    color: var(--ink);
  }
  .brand {
    position: absolute;
    left: 98px;
    top: 62px;
    display: flex;
    align-items: center;
    gap: 12px;
  }
  .brand-mark {
    width: 20px; height: 20px;
    border-radius: 50%;
    background: var(--brand-pink);
  }
  .brand-name {
    font-size: 36px;
    font-weight: 600;
    color: var(--brand-pink);
    letter-spacing: -0.5px;
  }
  .contact-top {
    position: absolute;
    right: 104px;
    top: 36px;
    font-family: "Lato", Arial, sans-serif;
    font-size: 18px;
    color: var(--ink-strong);
    text-align: right;
    line-height: 24px;
  }
  .contact-line { display: flex; justify-content: flex-end; align-items: center; gap: 5px; }
  .contact-line svg { width: 16px; height: 16px; fill: var(--brand-pink); }
  .letter-body {
    position: absolute;
    left: 97px;
    width: 840px;
    top: 217px;
    font-size: 15.5px;
  }
  .issue-date { margin-bottom: 16px; }
  .recipient { line-height: 19px; margin-bottom: 52px; }
  .salutation { margin-bottom: 28px; }
  .paragraph {
    line-height: 27.2px;
    text-align: justify;
    margin-bottom: 27px;
  }
  .closing { margin-top: 56px; }
  .signatory {
    margin-top: 56px;
    font-size: 20px;
    font-weight: 600;
    color: var(--ink-strong);
  }
  .signatory-role { margin-top: 6px; font-size: 15.5px; }
  .footer-wave { position: absolute; left: 0; top: 1000px; width: 1040px; height: 200px; }
  .footer-details {
    position: absolute;
    right: 108px;
    top: 1100px;
    font-family: "Lato", Arial, sans-serif;
    font-size: 19px;
    line-height: 22px;
    color: #ffffff;
    text-align: right;
  }
</style>
</head>
<body>
<main class="letterhead">
  <div class="brand">
    <span class="brand-mark"></span>
    <span class="brand-name">Bright Oak</span>
  </div>

  <div class="contact-top">
    <div class="contact-line">0461739286
      <svg viewBox="0 0 16 16" aria-hidden="true"><path d="M2 5c0-2 2-3 6-3s6 1 6 3v1h-3V5H5v1H2z M4 7h8l1 6H3z"/></svg>
    </div>
    <div class="contact-line">www.brightoakconveyancing.com.au
      <svg viewBox="0 0 16 16" aria-hidden="true"><circle cx="8" cy="8" r="7"/></svg>
    </div>
  </div>

  <section class="letter-body">
    <p class="issue-date">Issuing Date: May 5, 2018</p>
    <p class="recipient">Name Of Employee Mr. XYZABC<br>Address of Employee<br>Address Line 2 etc..</p>
    <p class="salutation">Dear Mr.XYZABC</p>
    <p class="paragraph">Lorem Ipsum has been the industry's standard dummy text ever since the 1500s, when an unknown printer took a galley of type and scrambled it to make a type specimen book. It has survived not only five centuries, but also the leap into electronic typesetting, remaining essentially unchanged. It was popularised in the 1960s with the release of Typeline sheets containing Lorem Ipsum passages, and more recently with desktop publishing software like Folio Layout including versions of Lorem Ipsum.</p>
    <p class="paragraph">Lorem Ipsum is simply dummy text of the printing and typesetting industry. Lorem Ipsum has been the industry's standard dummy text ever since the 1500s, when an unknown printer took a galley of type and scrambled it to make a type specimen book.</p>
    <p class="paragraph">It has survived not only five centuries, but also the leap into electronic typesetting, remaining essentially unchanged. It was popularised in the 1960s with the release of Typeline sheets containing Lorem IpsumIpsum passages.</p>
    <p class="closing">Yours Sincerely</p>
    <p class="signatory">Daniel Hartley</p>
    <p class="signatory-role">Managing Director</p>
  </section>

  <svg class="footer-wave" viewBox="0 0 1040 200" aria-hidden="true">
    <path d="M0,88 C120,122 270,140 430,120 C630,92 830,52 1040,56 L1040,200 L0,200 Z" fill="var(--brand-grey)"/>
    <path d="M0,88 C120,122 270,140 430,120 C630,92 830,52 1040,56" fill="none" stroke="#ffffff" stroke-width="3"/>
    <path d="M0,43 C110,92 280,108 621,82 C420,114 230,124 0,80 Z" fill="var(--brand-pink)"/>
  </svg>

  <div class="footer-details">
    <p>Bright Oak Conveyancing Pty Ltd</p>
    <p>ACN 583 217 469</p>
    <p>PO Box 871 Marlowdale SA 5096</p>
  </div>
</main>
</body>
</html>
```